Hearthside Lending Relief

Please help us give our website a remake or a FACELIFT. It is not very good but it says what we need it to say. But the design is terrible.
I would like our new design font and logo to be used as the theme.

I also want more photos on the site.

I also want consistency with the pages so they look clean.

We want the professionals to do this, let's see what you got!

Thank you!
Updates

Project Deadline Extended
Reason: I can understand you want to be paid. So I will commit to the fee but I want you to have time to make a KICK ASS website for me dudes! Thanks

HI!  Just wanted to say thanks for your time on these.  A lot are great.  However the firefighters have nothing to do with Foreclosure.  We are saving peoples homes from the bank taking them and selling them.   I LOVE the house photos and the families on the website.  That is the direction we like.  THanks.

THANK U ALL FOR THE WORK!   I like a few ending in the numbers: 147  733  693  536  620  478  727  508     I will go over them and choose one soon.  Thank you.   You will be paid shortly. 

Requirements
Must have
• Bright, Upbeat photos. Color scheme should be in order. We like icons on the bottom. not just text.

```html
<!DOCTYPE html>
<html lang="en">
<head>
<meta charset="utf-8">
<title>Services – Hearthside Lending Relief</title>
<link href="https://fonts.googleapis.com/css2?family=Noto+Sans:wght@400;700&display=swap" rel="stylesheet">
<style>
:root{
  --red:#d9222a;
  --ink:#222222;
  --body:#4a4a4a;
  --grey:#7a7a7a;
  --panel:#e1e1e1;
  --black:#000000;
  --white:#ffffff;
  --field:#d4d4d4;
}
*{margin:0;padding:0;box-sizing:border-box}
html,body{width:1200px;height:857px;overflow:hidden;background:var(--white)}
body{font-family:"Noto Sans",Arial,sans-serif;color:var(--body);position:relative}
.brand{position:absolute;left:108px;top:28px;display:flex;align-items:center;gap:16px}
.brand-dot{width:96px;height:96px;border-radius:50%;background:var(--red)}
.brand-name{font-weight:700;font-size:26px;line-height:30px;color:var(--ink);text-transform:uppercase}
.hotline{position:absolute;left:846px;top:50px;display:flex;gap:12px}
.hotline-number{font-size:28px;line-height:34px;color:var(--grey);margin-top:4px}
.hotline-cta{font-size:20px;line-height:22px;color:var(--red)}
.main-nav{position:absolute;left:0;top:156px;width:1200px;height:26px;background:var(--black)}
.main-nav a{position:absolute;top:0;height:26px;line-height:26px;color:var(--white);font-size:13.5px;text-decoration:none;text-align:center}
.main-nav .sep{position:absolute;top:0;width:4px;height:26px;background:var(--white)}
.search-field{position:absolute;left:960px;top:3px;width:150px;height:19px;background:var(--field)}
.search-icon{position:absolute;left:934px;top:3px}
.content{position:absolute;left:88px;top:190px;width:712px}
.page-title{color:var(--red);font-size:20px;font-weight:700;line-height:28px}
.content p{font-size:13px;line-height:16.5px;text-align:justify;margin-top:10px}
.solutions-title{color:var(--red);font-size:20px;line-height:24px;font-weight:400;margin-top:22px}
.solutions{display:flex;margin-top:26px;gap:38px}
.solution{width:118px}
.solution-icon{width:112px;height:88px;background:linear-gradient(180deg,#e44a4f 0%,#8a8a8a 60%,#6f6f6f 100%);border-radius:4px}
.solution-text{font-size:13.5px;line-height:16.5px;color:var(--ink);text-align:justify;margin-top:10px}
.more{margin-top:44px}
.more p{margin-top:16px}
.more p:first-child{margin-top:0}
.testimonials{position:absolute;left:816px;top:185px;width:297px;height:585px;background:var(--panel)}
.testimonials-head{height:35px;background:var(--red);display:flex;align-items:center;gap:10px;padding-left:16px;color:var(--white);font-weight:700;font-size:20px}
.quote{padding:0 20px 0 18px;font-size:13.5px;line-height:15px;color:var(--grey);text-align:justify}
.quote:first-of-type{margin-top:12px}
.quote + .quote{margin-top:16px}
.quote cite{display:block;text-align:right;font-style:normal;margin-top:6px}
.footer-nav{position:absolute;left:88px;top:776px;width:1025px;height:34px;background:var(--black);color:var(--white);font-size:13.5px;line-height:34px;padding-left:13px}
.legal{position:absolute;top:820px;font-size:13px;color:var(--body)}
</style>
</head>
<body>
<header>
  <div class="brand">
    <span class="brand-dot"></span>
    <span class="brand-name">Hearthside<br>Lending<br>Relief</span>
  </div>
  <div class="hotline">
    <svg width="46" height="46" viewBox="0 0 46 46" aria-hidden="true">
      <circle cx="23" cy="23" r="21" fill="none" stroke="#7a7a7a" stroke-width="3"/>
      <path d="M15 12c2-2 4-1 5 1l2 4c1 2 0 3-1 4l-1 1c1 3 3 5 6 6l1-1c1-1 2-2 4-1l4 2c2 1 3 3 1 5l-2 2c-9 1-20-10-19-19z" fill="#7a7a7a"/>
    </svg>
    <div>
      <div class="hotline-number">877.555.0142</div>
      <div class="hotline-cta">Call Tall Free Now</div>
    </div>
  </div>
</header>

<nav class="main-nav">
  <a href="#" style="left:88px;width:109px">HOME</a>
  <span class="sep" style="left:197px"></span>
  <a href="#" style="left:201px;width:151px">WHO WE ARE</a>
  <span class="sep" style="left:352px"></span>
  <a href="#" style="left:356px;width:124px">SERVICES</a>
  <span class="sep" style="left:480px"></span>
  <a href="#" style="left:484px;width:192px">FINANCING OPTIONS</a>
  <span class="sep" style="left:676px"></span>
  <a href="#" style="left:680px;width:122px">CONTACT US</a>
  <span class="sep" style="left:810px;width:6px"></span>
  <a href="#" style="left:816px;width:104px">SPANISH</a>
  <svg class="search-icon" width="22" height="20" viewBox="0 0 22 20" aria-hidden="true">
    <circle cx="8" cy="8" r="6" fill="none" stroke="#fff" stroke-width="2.5"/>
    <line x1="12.5" y1="12.5" x2="19" y2="18" stroke="#fff" stroke-width="3"/>
  </svg>
  <span class="search-field"></span>
</nav>

<main class="content">
  <h1 class="page-title">SERVICES</h1>
  <p>HEARTHSIDE LENDING RELIEF starts working for you the moment you make contact with us without any cost to you. There is no need for you to face this process alone. There are many alternatives to the painful process of foreclosure. Having your home foreclosed on can be an embarrassing situation that can damage your self-esteem and put a terrible mark on your credit for up to 7 years. By completing our free consultation form or calling us today, we will analyze your situation immediately and provide you a strategic plan that can help you avoid foreclosure.</p>
  <h2 class="solutions-title">SOME OF THE SOLUTIONS OUR SPECIALIST CAN DISCUSS WITH YOU ARE:</h2>
  <div class="solutions">
    <div class="solution"><div class="solution-icon" role="img" aria-label="House icon with magnifying glass"></div><div class="solution-text">Review and update your mortgage to stop forclosure</div></div>
    <div class="solution"><div class="solution-icon" role="img" aria-label="For sale sign icon"></div><div class="solution-text">We can purchase your home with CASH in 7-10 days</div></div>
    <div class="solution"><div class="solution-icon" role="img" aria-label="House icon with dollar sign"></div><div class="solution-text">We offer Financing and different Purchase Options</div></div>
    <div class="solution"><div class="solution-icon" role="img" aria-label="House icon with moving truck"></div><div class="solution-text">Relocations Assistance if needed</div></div>
    <div class="solution"><div class="solution-icon" role="img" aria-label="House icon with ladder"></div><div class="solution-text">We help you remodel your home to increase it's value</div></div>
  </div>
  <div class="more">
    <p>Many other options are available - We realize that all of our clients have different needs. We look at your individual needs to customize a solution just for you.</p>
    <p>Our evaluations are free of charge, so you have nothing to loose, contact us today!</p>
    <p>As you can see, we have many methods to resolve your situation. You do not have to give up and settle with the bank foreclosing on your home. All you have to do is give us a call or fill out our free consultation form, we will start working for you immediately.</p>
    <p>There is no need to sit back and lose your home, let HEARTHSIDE LENDING RELIEF help you keep that from happening.</p>
  </div>
</main>

<aside class="testimonials">
  <div class="testimonials-head">
    <svg width="30" height="28" viewBox="0 0 30 28" aria-hidden="true">
      <path d="M3 3h24v16H12l-7 6v-6H3z" fill="none" stroke="#fff" stroke-width="3" stroke-linejoin="round"/>
    </svg>
    TESTIMONIALS
  </div>
  <blockquote class="quote">“Dear Dan,<br>I'd like to express my gratitude to you and your company and I have to add, for all of the trustworthy and reliable service that you bring to the public. Your company helped put me back together, you in particular are awesome! Thank you again Dan.”<cite>- Greta</cite></blockquote>
  <blockquote class="quote">“Hearthside Lending Relief has been an absolute life saver for me and my family. Their services have changed everything. Instead of my house going into foreclosure and losing everything I own, I now have a chance to start over and the money to do it with! They've been fast, friendly and efficient. I would recommend their services to anyone facing foreclosure.”<cite>- Lorraine P.</cite></blockquote>
  <blockquote class="quote">“I owe you guys a big thank you. The stress of this whole thing was almost too much for me. I didn't believe that you could help at first to be honest. You have done everything you said you would and you were very considerate of us. We are pleased to have been able to dictate our own choices in this and to walk away with more money than we expected.Thanks again guys.”<cite>- Walter M.</cite></blockquote>
</aside>

<footer>
  <nav class="footer-nav">Home I Who We Are I Services I Financial Options I Contact Us</nav>
  <div class="legal" style="left:99px">© 2012 HEARTHSIDELENDINGRELIEF.COM. All rights reserved.</div>
  <div class="legal" style="right:104px">618 Larkspur Avenue, Suite 300, Fairview, CA 92020, 877.555.0142</div>
</footer>
</body>
</html>
```